We are a recruitment company based in Norwich/Cambridge England.
I have included our company logo which we want to remain the same.

What we are looking for is a new creative Business card which will really stand out!!

Contact Information for Business Card

Harriet Dunmore
email: Harriet@plavex.co.uk
Address: Brackwell House
Fenmoor Enterprise Park
Partridge Way
Norwich
QB9 3KX
Tel:01632 960418

```html
<!DOCTYPE html>
<html lang="en">
<head>
<meta charset="utf-8">
<title>Plavex Business Card</title>
<link rel="stylesheet" href="https://fonts.googleapis.com/css2?family=Roboto:wght@400;500;700&display=swap">
<style>
  :root {
    --green-dark: #62a52a;
    --green-light: #a8d052;
    --green-text: #7cbc34;
    --grey-band: #9d9ca1;
    --grey-text: #8a898e;
    --ink: #5e5d62;
    --card-white: #ffffff;
    --card-shade: #e6e6e6;
    --stage: #ecece9;
  }
  * { margin: 0; padding: 0; box-sizing: border-box; }
  html, body {
    width: 1200px; height: 780px; overflow: hidden;
    background: var(--stage);
    font-family: "Roboto", Arial, sans-serif;
  }
  .sheet {
    position: relative; width: 1200px; height: 780px;
  }
  .card {
    position: absolute; top: 235px;
    width: 540px; height: 309px;
    border-radius: 16px; overflow: hidden;
    background: linear-gradient(160deg, var(--card-white) 40%, var(--card-shade) 100%);
    box-shadow: 0 8px 22px rgba(0,0,0,0.14);
  }
  .card--front { left: 40px; }
  .card--back  { left: 620px; }
  .card__art { position: absolute; inset: 0; width: 100%; height: 100%; }

  .brand { position: absolute; display: flex; align-items: center; gap: 10px; }
  .brand__dot { width: 30px; height: 30px; border-radius: 50%; background: var(--grey-band); flex: none; }
  .brand__name { font-weight: 700; font-size: 40px; line-height: 1; color: var(--green-text); letter-spacing: -0.5px; }
  .brand__tagline {
    font-size: 8px; letter-spacing: 2.6px; color: var(--grey-text);
    margin-top: 3px; white-space: nowrap;
  }
  .card--front .brand { left: 34px; top: 40px; }
  .card--back .brand { left: 50%; top: 50%; transform: translate(-50%, -58%); }

  .person { position: absolute; left: 36px; top: 134px; }
  .person__name { font-weight: 700; font-size: 20px; color: var(--green-text); }
  .person__role { font-size: 12px; color: var(--grey-text); margin-top: 1px; }

  .contacts { position: absolute; left: 36px; top: 190px; list-style: none; }
  .contacts__item {
    display: flex; align-items: flex-start; gap: 7px;
    font-size: 11px; line-height: 15px; color: var(--ink); margin-bottom: 5px;
  }
  .contacts__icon { width: 14px; height: 14px; flex: none; margin-top: 0.5px; }

  .website {
    position: absolute; right: 22px; bottom: 16px;
    font-size: 11px; color: #ffffff; letter-spacing: 0.3px;
  }
</style>
</head>
<body>
<main class="sheet">

  <section class="card card--front" aria-label="Front of business card">
    <svg class="card__art" viewBox="0 0 540 309" preserveAspectRatio="none" aria-hidden="true">
      <defs>
        <linearGradient id="frontGreen" x1="0" y1="1" x2="1" y2="0">
          <stop offset="0" stop-color="var(--green-dark)"/>
          <stop offset="1" stop-color="var(--green-light)"/>
        </linearGradient>
        <linearGradient id="frontGrey" x1="0" y1="1" x2="1" y2="0">
          <stop offset="0" stop-color="#b4b3b8"/>
          <stop offset="1" stop-color="var(--grey-band)"/>
        </linearGradient>
      </defs>
      <path d="M250 309 C360 232 450 150 540 40 L540 74 C462 170 382 250 302 309 Z" fill="url(#frontGrey)"/>
      <path d="M310 309 C396 244 472 174 540 96 L540 309 Z" fill="url(#frontGreen)"/>
    </svg>

    <div class="brand">
      <span class="brand__dot"></span>
      <div>
        <div class="brand__name">Plavex</div>
        <div class="brand__tagline">Technology Recruitment</div>
      </div>
    </div>

    <div class="person">
      <div class="person__name">Harriet Dunmore</div>
      <div class="person__role">CEO</div>
    </div>

    <ul class="contacts">
      <li class="contacts__item">
        <svg class="contacts__icon" viewBox="0 0 14 14" aria-hidden="true">
          <circle cx="7" cy="7" r="7" fill="var(--green-text)"/>
          <rect x="3.5" y="4.5" width="7" height="5" rx="0.6" fill="#fff"/>
          <path d="M3.7 4.8 L7 7.3 L10.3 4.8" fill="none" stroke="var(--green-text)" stroke-width="0.8"/>
        </svg>
        <span>Harriet@plavex.co.uk</span>
      </li>
      <li class="contacts__item">
        <svg class="contacts__icon" viewBox="0 0 14 14" aria-hidden="true">
          <circle cx="7" cy="7" r="7" fill="var(--green-text)"/>
          <rect x="4.8" y="3" width="4.4" height="8" rx="0.9" fill="#fff"/>
          <rect x="5.6" y="4" width="2.8" height="4.8" fill="var(--green-text)"/>
        </svg>
        <span>01632 960418</span>
      </li>
      <li class="contacts__item">
        <svg class="contacts__icon" viewBox="0 0 14 14" aria-hidden="true">
          <circle cx="7" cy="7" r="7" fill="var(--green-text)"/>
          <path d="M7 11.2 C5 8.8 4.3 7.6 4.3 6.2 A2.7 2.7 0 0 1 9.7 6.2 C9.7 7.6 9 8.8 7 11.2 Z" fill="#fff"/>
          <circle cx="7" cy="6.2" r="1" fill="var(--green-text)"/>
        </svg>
        <span>Brackwell House, Fenmoor Enterprise Park<br>Partridge Way, Norwich, QB9 3KX</span>
      </li>
    </ul>

    <div class="website">www.plavex.co.uk</div>
  </section>

  <section class="card card--back" aria-label="Back of business card">
    <svg class="card__art" viewBox="0 0 540 309" preserveAspectRatio="none" aria-hidden="true">
      <defs>
        <linearGradient id="backGreen" x1="0" y1="0" x2="1" y2="1">
          <stop offset="0" stop-color="var(--green-dark)"/>
          <stop offset="1" stop-color="var(--green-light)"/>
        </linearGradient>
      </defs>
      <path d="M0 0 H540 V30 C360 42 160 70 0 104 Z" fill="url(#backGreen)"/>
      <path d="M0 104 C160 70 360 42 540 30 L540 38 C360 56 170 92 0 124 Z" fill="var(--grey-band)"/>
      <path d="M540 309 H0 V282 C180 272 380 244 540 206 Z" fill="url(#backGreen)"/>
      <path d="M540 206 C380 244 180 272 0 282 L0 276 C190 258 380 222 540 186 Z" fill="var(--grey-band)"/>
    </svg>

    <div class="brand">
      <span class="brand__dot"></span>
      <div>
        <div class="brand__name">Plavex</div>
        <div class="brand__tagline">Technology Recruitment</div>
      </div>
    </div>
  </section>

</main>
</body>
</html>
```